Online interactive tutorial for year 2 to year 12 students in Australia

Website design for a new online tutorial for year 2 to year 12 students in Australia.

- The tutorial will be conducted via live webcam and within a dedicated interactive space
- The tutorial will be provided by high scoring undergraduates studying in top Australian universities.
- The tutors will be going through interviews & assessments & only top students are allowed to apply.
- Parents will do search and select tutor and have short 15 mins video interaction with potential tutors before booking them for their children for tutoring.
- hourly cost of booking (no monthly subscription or no hour limits)
- Tutors will have their own profile

Please see the attached for detailed page functionality.

The look and feel of the design must consider the following:
- must be educational but not dull and should stand out
- must appeal to younger generation - tutees (8-18 years), tutors (19-25), parents (30-50).
- Ideas for Logos (brivora.com.au but not confirmed)

Target Market(s)

tutees (8-18 years), tutors (19-25 years), parents (30-50 years).

Industry/Entity Type

Education

Coding

Coded - Design and coding required

Number of Pages Required

5+ page

Font styles to use
Serif

Requirements
Must have
• The look and feel of the design must consider the following:
• - must be educational but not dull and should stand out
• - must appeal to younger generation - tutees (8-18 years), tutors (19-25), parents (30-50).
Should not have
• Dullness

```html
<!DOCTYPE html>
<html lang="en">
<head>
<meta charset="utf-8">
<title>Brivora — Online Tutoring for Kids</title>
<link href="https://fonts.googleapis.com/css2?family=Raleway:wght@300;400;500;600;700;800&family=Open+Sans:wght@400;600;700&display=swap" rel="stylesheet">
<style>
:root{
  --blue:#2f86c6;
  --ink:#222428;
  --text:#6f7378;
  --muted:#9a9ea3;
  --rule:#e4e6e8;
  --footer:#efefef;
  --footer-base:#ffffff;
  --teal:#5f8c98;
  --olive:#b7b38a;
  --white:#ffffff;
  --mark:#6d6e70;
}
*{box-sizing:border-box;margin:0;padding:0}
html,body{width:1200px;height:3516px;overflow:hidden}
body{position:relative;background:var(--white);font-family:"Open Sans",Arial,sans-serif;color:var(--text)}
.abs{position:absolute}
h2.section-title{position:absolute;left:0;width:1200px;text-align:center;font-family:"Raleway",Arial,sans-serif;font-weight:700;font-size:28px;letter-spacing:1px;color:var(--ink)}
p.section-sub{position:absolute;left:0;width:1200px;text-align:center;font-size:13px;color:var(--text)}

/* hero */
.hero{left:0;top:0;width:1200px;height:703px;
  background:
    radial-gradient(ellipse 210px 230px at 250px 190px, rgba(236,205,150,.95), rgba(236,205,150,0) 70%),
    radial-gradient(ellipse 150px 120px at 300px 330px, rgba(238,190,165,.9), rgba(238,190,165,0) 70%),
    radial-gradient(ellipse 260px 280px at 400px 520px, rgba(205,208,212,.95), rgba(205,208,212,0) 70%),
    radial-gradient(ellipse 190px 170px at 600px 150px, rgba(110,75,50,.95), rgba(110,75,50,0) 70%),
    radial-gradient(ellipse 150px 130px at 620px 300px, rgba(228,180,150,.9), rgba(228,180,150,0) 70%),
    radial-gradient(ellipse 240px 220px at 600px 560px, rgba(85,105,65,.9), rgba(85,105,65,0) 70%),
    radial-gradient(ellipse 230px 300px at 860px 280px, rgba(150,100,65,.95), rgba(150,100,65,0) 70%),
    radial-gradient(ellipse 130px 120px at 840px 330px, rgba(240,196,170,.9), rgba(240,196,170,0) 70%),
    radial-gradient(ellipse 300px 200px at 900px 620px, rgba(232,222,232,.95), rgba(232,222,232,0) 70%),
    radial-gradient(ellipse 200px 260px at 80px 380px, rgba(120,140,110,.8), rgba(120,140,110,0) 70%),
    linear-gradient(100deg,#c97a3e 0%,#dca062 28%,#c08a5c 55%,#b1653c 78%,#7f5236 100%)}
.hero::after{content:"";position:absolute;inset:0;background:linear-gradient(rgba(20,20,25,.25),rgba(20,20,25,.12) 40%,rgba(20,20,25,.3))}
.brand{left:98px;top:38px;z-index:2;font-family:"Raleway",Arial,sans-serif;font-weight:500;font-size:40px;color:var(--white)}
.main-nav a{position:absolute;top:60px;z-index:2;white-space:nowrap;font-family:"Raleway",Arial,sans-serif;font-size:12px;font-weight:500;color:var(--white);text-decoration:none;letter-spacing:.3px}
.play{left:548px;top:283px;z-index:2}
.hero-title{left:0;top:410px;width:1200px;z-index:2;text-align:center;font-family:"Raleway",Arial,sans-serif;font-weight:400;font-size:31px;line-height:46px;color:var(--white)}
.scroll{left:588px;top:598px;z-index:2}
.slide-dots{left:1158px;top:312px;z-index:2;display:flex;flex-direction:column;gap:16px}
.slide-dots span{width:9px;height:9px;border-radius:50%;background:rgba(255,255,255,.6)}

/* features */
.feature{top:783px;width:300px;text-align:center}
.feature .icon{width:86px;height:86px;border-radius:50%;background:var(--blue);margin:0 auto;display:flex;align-items:center;justify-content:center}
.feature h3{margin-top:32px;font-family:"Raleway",Arial,sans-serif;font-weight:700;font-size:14px;color:var(--ink);letter-spacing:.5px}
.feature p{margin:18px auto 0;width:256px;font-size:12px;line-height:24px;color:var(--text)}

/* services */
.service{top:1177px;width:321px}
.service .photo{width:321px;height:215px}
.service h3{margin-top:22px;font-family:"Raleway",Arial,sans-serif;font-weight:700;font-size:13px;color:var(--ink)}
.service p{margin-top:8px;font-size:12px;line-height:24px;color:var(--text);width:270px}
.photo-webcam{background:
  radial-gradient(ellipse 80px 80px at 100px 70px, rgba(225,185,110,.95), rgba(225,185,110,0) 70%),
  radial-gradient(ellipse 70px 80px at 230px 80px, rgba(235,200,120,.95), rgba(235,200,120,0) 70%),
  radial-gradient(ellipse 90px 60px at 240px 190px, rgba(240,100,150,.9), rgba(240,100,150,0) 70%),
  radial-gradient(ellipse 90px 50px at 220px 150px, rgba(170,200,225,.8), rgba(170,200,225,0) 70%),
  radial-gradient(ellipse 110px 60px at 70px 190px, rgba(200,200,205,.9), rgba(200,200,205,0) 70%),
  linear-gradient(135deg,#f4efe8,#f7f3ee 50%,#e9e4df)}
.photo-interviews{background:
  radial-gradient(ellipse 60px 110px at 40px 100px, rgba(90,140,180,.8), rgba(90,140,180,0) 70%),
  radial-gradient(ellipse 70px 70px at 110px 110px, rgba(90,60,40,.9), rgba(90,60,40,0) 70%),
  radial-gradient(ellipse 70px 60px at 170px 175px, rgba(225,100,120,.85), rgba(225,100,120,0) 70%),
  radial-gradient(ellipse 70px 90px at 250px 60px, rgba(180,120,70,.9), rgba(180,120,70,0) 70%),
  radial-gradient(ellipse 60px 80px at 270px 180px, rgba(50,60,80,.85), rgba(50,60,80,0) 70%),
  linear-gradient(100deg,#6f8fa6,#c8b49a 40%,#d9cdbd 70%,#8c7f72)}
.photo-undergrads{background:
  radial-gradient(ellipse 80px 70px at 150px 70px, rgba(110,70,45,.9), rgba(110,70,45,0) 70%),
  radial-gradient(ellipse 70px 60px at 160px 150px, rgba(235,180,150,.85), rgba(235,180,150,0) 70%),
  radial-gradient(ellipse 70px 80px at 260px 90px, rgba(225,180,100,.95), rgba(225,180,100,0) 70%),
  radial-gradient(ellipse 80px 60px at 260px 200px, rgba(60,100,170,.9), rgba(60,100,170,0) 70%),
  radial-gradient(ellipse 60px 90px at 30px 130px, rgba(190,195,200,.9), rgba(190,195,200,0) 70%),
  linear-gradient(100deg,#d88a3c,#efb36a 45%,#e0944a 75%,#b86d35)}

/* tutors */
.tutor{top:1675px;width:150px;text-align:center}
.tutor .avatar{width:146px;height:146px;border-radius:50%;margin:0 auto;border:3px solid #e9e9e9}
.tutor h4{margin-top:28px;font-family:"Raleway",Arial,sans-serif;font-weight:700;font-size:12px;color:var(--ink);letter-spacing:.3px}
.av1{background:radial-gradient(circle at 50% 45%,#e6b99a 0,#d9a27e 28%,#b88a4a 45%,#4d5d6e 80%)}
.av2{background:radial-gradient(circle at 50% 45%,#efc7a8 0,#e4b393 30%,#8c5a38 46%,#b9b9bd 80%)}
.av3{background:radial-gradient(circle at 50% 45%,#f0c6aa 0,#e2ab87 28%,#6b3f28 48%,#c9b49f 82%)}
.av4{background:radial-gradient(circle at 50% 45%,#f3d1b8 0,#e6bb9c 28%,#a8734c 48%,#d9cfc7 82%)}
.av5{background:radial-gradient(circle at 50% 45%,#ecc0a0 0,#d99e7c 28%,#5a2e22 48%,#a8322e 70%,#e2d8d2 90%)}

/* scheduler */
.scheduler{left:0;top:1945px;width:1200px;height:462px;background:
  radial-gradient(ellipse 260px 200px at 900px 130px, rgba(150,110,80,.9), rgba(150,110,80,0) 70%),
  radial-gradient(ellipse 300px 180px at 930px 390px, rgba(40,130,130,.9), rgba(40,130,130,0) 70%),
  radial-gradient(ellipse 200px 160px at 1100px 110px, rgba(130,170,175,.8), rgba(130,170,175,0) 70%),
  radial-gradient(ellipse 260px 160px at 600px 420px, rgba(60,60,65,.95), rgba(60,60,65,0) 70%),
  linear-gradient(100deg,#555a5f 0%,#6a6e70 40%,#7a7670 70%,#5d6668 100%)}
.scheduler::after{content:"";position:absolute;inset:0;background:rgba(25,28,32,.4)}
.calendar{left:141px;top:2027px;width:391px;height:300px;background:var(--white);z-index:2;box-shadow:0 2px 8px rgba(0,0,0,.25)}
.cal-head{height:47px;display:flex;align-items:center;justify-content:space-between;border-bottom:1px solid var(--rule)}
.cal-head .arrow{width:22px;height:47px;background:var(--teal);display:flex;align-items:center;justify-content:center}
.cal-head h4{font-family:"Raleway",Arial,sans-serif;font-weight:700;font-size:14px;color:#4a4d52;letter-spacing:.5px}
.cal-grid{margin:10px auto 0;border-collapse:collapse;width:357px;table-layout:fixed}
.cal-grid th{font-family:"Raleway",Arial,sans-serif;font-size:11px;font-weight:700;color:#444;height:28px}
.cal-grid td{border:1px solid var(--rule);height:36px;text-align:center;font-size:11px;color:#555}
.cal-grid td.out{color:#c9c9c9}
.cal-grid td.today{background:var(--olive);color:var(--white)}
.sched-title{left:605px;top:2030px;z-index:2;font-family:"Raleway",Arial,sans-serif;font-weight:700;font-size:26px;color:var(--white)}
.event{left:608px;width:520px;z-index:2}
.event h5{font-family:"Raleway",Arial,sans-serif;font-weight:600;font-size:11px;color:var(--white);letter-spacing:.3px}
.event hr{width:64px;border:0;border-top:2px solid var(--white);margin:14px 0 14px}
.event p{font-size:12px;line-height:26px;color:#eeeeee}

/* payment */
.pay-row{left:100px;top:2618px;width:1000px;display:flex;justify-content:space-between;align-items:center}
.pay-row span{font-family:"Raleway",Arial,sans-serif;font-weight:800;font-size:34px;color:var(--mark);letter-spacing:.5px}
.pay-row span.small{font-size:26px}

/* feedback */
.feedback{left:0;top:2766px;width:1200px;height:414px;background:var(--blue)}
.feedback h2.section-title,.feedback p.section-sub{color:var(--white)}
.quote{top:2930px;width:330px}
.quote .q{font-family:Georgia,serif;font-size:30px;color:var(--white);line-height:1}
.quote p{margin:-14px 0 0 20px;width:290px;font-size:11.5px;line-height:24px;color:var(--white)}
.quote .q-end{text-align:right;margin-right:18px;margin-top:-6px}
.quote .who{display:flex;align-items:center;margin-top:16px}
.quote .face{width:52px;height:52px;border-radius:50%;border:3px solid var(--white);background:radial-gradient(circle at 50% 48%,#f1c9a8 0,#e3b08c 30%,#7a4a2e 48%,#dfe4ea 75%)}
.quote .who h6{margin-left:18px;font-family:"Raleway",Arial,sans-serif;font-weight:700;font-size:11px;color:var(--white)}
.quote .who small{display:block;margin-top:4px;font-family:"Open Sans",Arial,sans-serif;font-weight:400;font-size:10.5px}

/* footer */
.site-footer{left:0;top:3180px;width:1200px;height:261px;background:var(--footer)}
.f-col{top:3222px}
.f-col h5{font-family:"Raleway",Arial,sans-serif;font-weight:700;font-size:12px;color:var(--blue);letter-spacing:.3px;margin-bottom:16px}
.f-col p,.f-col li{font-size:11px;line-height:26px;color:var(--muted);list-style:none}
.f-col .more{display:inline-flex;align-items:center;gap:8px;margin-top:14px;font-family:"Raleway",Arial,sans-serif;font-weight:700;font-size:11px;color:var(--blue)}
.f-col .line{display:flex;align-items:center;gap:12px}
.footer-base{left:0;top:3441px;width:1200px;height:75px;background:var(--footer-base)}
.copy{left:103px;top:3470px;font-size:11px;color:var(--muted)}
.social{left:776px;top:3468px;display:flex;align-items:center;gap:16px;font-size:11px;color:var(--muted)}
.social b{font-weight:600;color:var(--blue);font-size:11px}
</style>
</head>
<body>

<!-- hero -->
<section class="abs hero" role="img" aria-label="Photo of three children looking together at a laptop in a classroom"></section>
<div class="abs brand">Brivora</div>
<nav class="main-nav">
  <a href="#" style="left:420px">HOME</a>
  <a href="#" style="left:523px">ABOUT</a>
  <a href="#" style="left:631px">SERVICES</a>
  <a href="#" style="left:754px">TUTOR PROFILE</a>
  <a href="#" style="left:910px">SCHEDULER</a>
  <a href="#" style="left:1045px">TESTIMONIALS</a>
</nav>
<svg class="abs play" width="104" height="104" viewBox="0 0 104 104"><circle cx="52" cy="52" r="49" fill="none" stroke="rgba(255,255,255,.8)" stroke-width="4"/><path d="M42 33 L72 52 L42 71 Z" fill="rgba(255,255,255,.85)"/></svg>
<h1 class="abs hero-title">We are an online training<br>website for kids from 2 years to 12 years</h1>
<svg class="abs scroll" width="24" height="56" viewBox="0 0 24 56"><rect x="3" y="2" width="18" height="30" rx="9" fill="none" stroke="#fff" stroke-width="2"/><line x1="12" y1="9" x2="12" y2="16" stroke="#fff" stroke-width="2"/><path d="M5 38 L12 45 L19 38 M5 45 L12 52 L19 45" fill="none" stroke="#fff" stroke-width="2"/></svg>
<div class="abs slide-dots"><span></span><span></span><span></span></div>

<!-- features -->
<div class="abs feature" style="left:110px">
  <div class="icon"><svg width="40" height="40" viewBox="0 0 40 40"><rect x="6" y="8" width="24" height="24" rx="3" fill="none" stroke="#fff" stroke-width="2.5"/><path d="M16 24 L17 19 L30 6 L34 10 L21 23 Z" fill="#fff"/></svg></div>
  <h3>TUTOR REGISTRATION</h3>
  <p>Es simplemente el texto de relleno de las imprentas y archivos de texto. Lorem Ipsum ha sido el texto de relleno...</p>
</div>
<div class="abs feature" style="left:452px">
  <div class="icon"><svg width="42" height="40" viewBox="0 0 42 40"><circle cx="21" cy="12" r="6" fill="#fff"/><circle cx="10" cy="15" r="4.5" fill="#fff"/><circle cx="32" cy="15" r="4.5" fill="#fff"/><path d="M12 32 C12 22 30 22 30 32 Z" fill="#fff"/><path d="M2 30 C2 22 13 21 15 25 L11 30 Z M40 30 C40 22 29 21 27 25 L31 30 Z" fill="#fff"/></svg></div>
  <h3>PARENT REGISTRATION</h3>
  <p>Es simplemente el texto de relleno de las imprentas y archivos de texto. Lorem Ipsum ha sido el texto de relleno...</p>
</div>
<div class="abs feature" style="left:797px">
  <div class="icon"><svg width="44" height="40" viewBox="0 0 44 40"><path d="M22 6 L42 15 L22 24 L2 15 Z" fill="none" stroke="#fff" stroke-width="2.5" stroke-linejoin="round"/><path d="M11 20 V29 C11 33 33 33 33 29 V20" fill="none" stroke="#fff" stroke-width="2.5"/><line x1="38" y1="17" x2="38" y2="28" stroke="#fff" stroke-width="2.5"/></svg></div>
  <h3>STUDENT LOG-INS</h3>
  <p>Es simplemente el texto de relleno de las imprentas y archivos de texto. Lorem Ipsum ha sido el texto de relleno...</p>
</div>

<!-- services -->
<h2 class="section-title" style="top:1068px">OUR SERVICES</h2>
<p class="section-sub" style="top:1116px">Es simplemente el texto de relleno de las imprentas y archivos de texto. Lorem Ipsum ha sido el texto...</p>
<div class="abs service" style="left:99px">
  <div class="photo photo-webcam" role="img" aria-label="Photo of a mother and daughter smiling in front of a laptop"></div>
  <h3>LIVE WEBCAM</h3>
  <p>Es simplemente el texto de relleno de las imprentas y archivos de texto...</p>
</div>
<div class="abs service" style="left:441px">
  <div class="photo photo-interviews" role="img" aria-label="Photo of smiling students in a classroom"></div>
  <h3>INTERVIEWS &amp; ASSESSMENTS</h3>
  <p>Es simplemente el texto de relleno de las imprentas y archivos de texto...</p>
</div>
<div class="abs service" style="left:783px">
  <div class="photo photo-undergrads" role="img" aria-label="Photo of a tutor helping children at a computer"></div>
  <h3>HIGH SCORING UNDERGRADUATES</h3>
  <p>Es simplemente el texto de relleno de las imprentas y archivos de texto...</p>
</div>

<!-- tutor profile -->
<h2 class="section-title" style="top:1546px">TUTOR PROFILE</h2>
<p class="section-sub" style="top:1596px">Es simplemente el texto de relleno de las imprentas y archivos de texto. Lorem Ipsum ha sido el texto...</p>
<div class="abs tutor" style="left:122px"><div class="avatar av1" role="img" aria-label="Portrait photo of a tutor"></div><h4>MILO BRENNAN</h4></div>
<div class="abs tutor" style="left:323px"><div class="avatar av2" role="img" aria-label="Portrait photo of a tutor"></div><h4>MILO BRENNAN</h4></div>
<div class="abs tutor" style="left:525px"><div class="avatar av3" role="img" aria-label="Portrait photo of a tutor"></div><h4>MILO BRENNAN</h4></div>
<div class="abs tutor" style="left:727px"><div class="avatar av4" role="img" aria-label="Portrait photo of a tutor"></div><h4>MILO BRENNAN</h4></div>
<div class="abs tutor" style="left:928px"><div class="avatar av5" role="img" aria-label="Portrait photo of a tutor"></div><h4>MILO BRENNAN</h4></div>

<!-- scheduler -->
<section class="abs scheduler" role="img" aria-label="Background photo of a child working at a computer"></section>
<div class="abs calendar">
  <div class="cal-head">
    <div class="arrow"><svg width="10" height="14" viewBox="0 0 10 14"><path d="M8 1 L2 7 L8 13" fill="none" stroke="#fff" stroke-width="2.5"/></svg></div>
    <h4>AUGUST</h4>
    <div class="arrow"><svg width="10" height="14" viewBox="0 0 10 14"><path d="M2 1 L8 7 L2 13" fill="none" stroke="#fff" stroke-width="2.5"/></svg></div>
  </div>
  <table class="cal-grid">
    <tr><th>Mon</th><th>Tue</th><th>Wed</th><th>Thu</th><th>Fri</th><th>Sat</th><th>Sun</th></tr>
    <tr><td>1</td><td>2</td><td>3</td><td>4</td><td>5</td><td>6</td><td>7</td></tr>
    <tr><td>8</td><td>9</td><td>10</td><td>11</td><td>12</td><td>13</td><td>14</td></tr>
    <tr><td>15</td><td>16</td><td>17</td><td>18</td><td>19</td><td>20</td><td>21</td></tr>
    <tr><td>22</td><td>23</td><td>24</td><td>25</td><td>26</td><td>27</td><td>28</td></tr>
    <tr><td>29</td><td class="today">30</td><td>31</td><td class="out">1</td><td class="out">2</td><td class="out">3</td><td class="out">4</td></tr>
  </table>
</div>
<h2 class="abs sched-title">SCHEDULER</h2>
<div class="abs event" style="top:2100px">
  <h5>ON 30 AUGUST 2016</h5><hr>
  <p>Es simplemente el texto de relleno de las imprentas y archivos de texto. Lorem Ipsum ha sido el texto de relleno estándar de las industrias desde...</p>
</div>
<div class="abs event" style="top:2228px">
  <h5>ON 30 AUGUST 2016</h5><hr>
  <p>Es simplemente el texto de relleno de las imprentas y archivos de texto. Lorem Ipsum ha sido el texto de relleno estándar de las industrias desde...</p>
</div>

<!-- payment -->
<h2 class="section-title" style="top:2490px">PAYMENT</h2>
<p class="section-sub" style="top:2540px">Es simplemente el texto de relleno de las imprentas y archivos de texto. Lorem Ipsum ha sido el texto...</p>
<div class="abs pay-row">
  <span>Paynest</span><span>Vantor</span><span class="small">Mercato</span><span class="small">Ardent Express</span><span>Dunmore</span>
</div>

<!-- feedback -->
<section class="abs feedback">
  <h2 class="section-title" style="top:52px">TUTOR FEEDBACK</h2>
  <p class="section-sub" style="top:104px">Es simplemente el texto de relleno de las imprentas y archivos de texto. Lorem Ipsum ha sido el texto...</p>
</section>
<div class="abs quote" style="left:100px">
  <div class="q">&ldquo;</div>
  <p>Lorem Ipsum is simply dummy text of the printing and typesetting industry. Lorem Ipsum has been the industry's standard dummy text ever since the 1500s printer took...</p>
  <div class="q q-end">&rdquo;</div>
  <div class="who"><div class="face" role="img" aria-label="Student portrait photo"></div><h6>MILO BRENNAN<small>Student</small></h6></div>
</div>
<div class="abs quote" style="left:452px">
  <div class="q">&ldquo;</div>
  <p>Lorem Ipsum is simply dummy text of the printing and typesetting industry. Lorem Ipsum has been the industry's standard dummy text ever since the 1500s printer took...</p>
  <div class="q q-end">&rdquo;</div>
  <div class="who"><div class="face" role="img" aria-label="Student portrait photo"></div><h6>MILO BRENNAN<small>Student</small></h6></div>
</div>
<div class="abs quote" style="left:804px">
  <div class="q">&ldquo;</div>
  <p>Lorem Ipsum is simply dummy text of the printing and typesetting industry. Lorem Ipsum has been the industry's standard dummy text ever since the 1500s printer took...</p>
  <div class="q q-end">&rdquo;</div>
  <div class="who"><div class="face" role="img" aria-label="Student portrait photo"></div><h6>MILO BRENNAN<small>Student</small></h6></div>
</div>

<!-- footer -->
<footer class="abs site-footer"></footer>
<div class="abs f-col" style="left:103px;width:330px">
  <h5>WHO WE ARE?</h5>
  <p>Lorem Ipsum is simply dummy text of the printing and typesetting industry. Lorem Ipsum has been the industry's standard dummy text ever since the 1500s, when an unknown printer took a galley of type and scrambled...</p>
  <span class="more">Read more info <svg width="12" height="12" viewBox="0 0 12 12"><circle cx="6" cy="6" r="6" fill="#2f86c6"/><path d="M5 3.5 L7.5 6 L5 8.5" fill="none" stroke="#fff" stroke-width="1.5"/></svg></span>
</div>
<div class="abs f-col" style="left:502px">
  <h5>WELCOME</h5>
  <ul><li>Home</li><li>About</li><li>Services</li><li>Tutor Profile</li><li>Scheduler</li><li>Testimonials</li></ul>
</div>
<div class="abs f-col" style="left:698px">
  <h5>INFORMATION</h5>
  <ul><li>Terms &amp; Conditions</li><li>Privacy policy</li><li>Disclaimer</li><li>Contact us</li><li>Sitemap</li></ul>
</div>
<div class="abs f-col" style="left:907px">
  <h5>CONTACT INFO</h5>
  <p>120 Street name, City name.<br>Country name : 3652235</p>
  <p class="line"><svg width="12" height="12" viewBox="0 0 12 12"><path d="M2 1 L5 1 L6 4 L4.5 5 C5 6.5 5.5 7 7 7.5 L8 6 L11 7 L11 10 C6 11 1 6 2 1 Z" fill="#2f86c6"/></svg>(02) 5550 1842</p>
  <p class="line"><svg width="12" height="10" viewBox="0 0 12 10"><rect width="12" height="10" rx="1" fill="#2f86c6"/><path d="M1 1.5 L6 5.5 L11 1.5" fill="none" stroke="#fff" stroke-width="1.2"/></svg>info@brivora.com.au</p>
</div>
<div class="abs footer-base"></div>
<p class="abs copy">© 2016, Brivora. All rights reserved</p>
<div class="abs social">Connect with our social network : <b>Kite</b><b>Loop</b><b>Orbi</b><b>Nook</b><b>Lume</b></div>

</body>
</html>
```